Flat Belly Design Graphics for Social

I want to create 9 social media graphics (new Instagram size 4:5 (1080 x 1350 pixels) focusing on our Flat Belly Graphics, using the pics attached. Use the attached pics, NO RANDOM STOCK PHOTOGRAPHY. For the color scheme of the graphics, the color palette is attached. YOU MUST POST ALL 9 GRAPHICS IN ONE ENTRY.
Using the 3 titles below, create one set of graphics. 1) with all text, then for the others, use the pictures as detailed below in IMPORTANT:
1. Ten-Week Bright Morning Reboot
2. The Quick Garden Kitchen Menu Guide
3. Studio Habits for Lasting Energy Past Midlife - Zero Gym Needed
IMPORTANT:
Only use RK Pic 1 and RK Pic 2 with the title, Ten-Week Bright Morning Reboot
Only use meal plan1 and meal plan2 pics with the title, Quick Garden Kitchen Menu Guide
Only use studio habits 1 and studio habits 2 pics with the title, Studio Habits for Lasting Energy Past Midlife - Zero Gym Needed
women over 40

```html
<!DOCTYPE html>
<html lang="en">
<head>
<meta charset="utf-8">
<title>Quick Garden Kitchen Menu Guide</title>
<link rel="stylesheet" href="https://fonts.googleapis.com/css2?family=Antonio:wght@100;200;500;600&family=Archivo+Black&family=Poppins:wght@300;400&display=swap">
<style>
  :root {
    --bg: #2f4d4b;
    --pink: #e197ae;
    --cream: #f8f4e6;
    --stripe: #5f7674;
    --mauve: #a9939b;
    --photo-dark: #4a3428;
    --photo-mid: #8a6a55;
    --photo-light: #e9d6cc;
  }
  * { margin: 0; padding: 0; box-sizing: border-box; }
  html, body { width: 960px; height: 1200px; overflow: hidden; background: var(--bg); }
  .poster { position: relative; width: 960px; height: 1200px; background: var(--bg); overflow: hidden; }

  .stripes { position: absolute; left: 0; top: 0; width: 132px; height: 318px; }

  .plus-marks { position: absolute; left: 43px; top: 474px; width: 92px; height: 34px; }

  .hero-photo {
    position: absolute; left: 543px; top: 27px; width: 746px; height: 746px; border-radius: 50%;
    background:
      radial-gradient(circle at 30% 30%, var(--photo-light) 0 14%, transparent 30%),
      radial-gradient(circle at 62% 66%, #f4f1ec 0 16%, transparent 32%),
      radial-gradient(circle at 18% 70%, #7f9a4a 0 8%, transparent 20%),
      linear-gradient(135deg, var(--photo-mid), var(--photo-dark));
  }

  .arc-text { position: absolute; left: 0; top: 0; width: 960px; height: 1200px; pointer-events: none; }
  .arc-text text { font-family: 'Poppins', sans-serif; font-weight: 300; font-size: 27px; letter-spacing: 9px; fill: var(--cream); }

  .tag-label {
    position: absolute; left: 48px; top: 569px; height: 44px; padding: 0 22px;
    background: var(--pink); color: var(--cream);
    font-family: 'Archivo Black', sans-serif; font-size: 34px; line-height: 44px; letter-spacing: 1px;
  }
  .title-top {
    position: absolute; left: 48px; top: 626px;
    font-family: 'Antonio', sans-serif; font-weight: 100; font-size: 122px; line-height: 1;
    color: var(--cream); letter-spacing: -1px; white-space: nowrap;
  }
  .title-main {
    position: absolute; left: 48px; top: 756px;
    font-family: 'Antonio', sans-serif; font-weight: 500; font-size: 158px; line-height: 1;
    color: var(--pink); letter-spacing: -1px; white-space: nowrap;
  }
  .tagline {
    position: absolute; left: 44px; top: 930px;
    font-family: 'Poppins', sans-serif; font-weight: 300; font-size: 43px; line-height: 1.2;
    color: var(--cream); white-space: nowrap;
  }

  .cta-band {
    position: absolute; left: 400px; top: 1047px; width: 560px; height: 69px;
    border-radius: 34px 0 0 34px;
    background: linear-gradient(90deg, var(--bg) 0%, #6f7f7c 35%, var(--mauve) 100%);
  }
  .web-address {
    position: absolute; left: 53px; top: 1062px;
    font-family: 'Poppins', sans-serif; font-weight: 400; font-size: 27px; line-height: 36px;
    color: var(--cream);
  }
  .cta-arrow { position: absolute; left: 362px; top: 1068px; width: 240px; height: 26px; }
</style>
</head>
<body>
<main class="poster">
  <svg class="stripes" viewBox="0 0 132 318" aria-hidden="true">
    <g stroke="var(--stripe)" stroke-width="2">
      <line x1="0" y1="1" x2="132" y2="1"/><line x1="0" y1="17.7" x2="132" y2="17.7"/>
      <line x1="0" y1="34.4" x2="132" y2="34.4"/><line x1="0" y1="51.1" x2="132" y2="51.1"/>
      <line x1="0" y1="67.8" x2="132" y2="67.8"/><line x1="0" y1="84.5" x2="132" y2="84.5"/>
      <line x1="0" y1="101.2" x2="132" y2="101.2"/><line x1="0" y1="117.9" x2="132" y2="117.9"/>
      <line x1="0" y1="134.6" x2="132" y2="134.6"/><line x1="0" y1="151.3" x2="132" y2="151.3"/>
      <line x1="0" y1="168" x2="132" y2="168"/><line x1="0" y1="184.7" x2="132" y2="184.7"/>
      <line x1="0" y1="201.4" x2="132" y2="201.4"/><line x1="0" y1="218.1" x2="132" y2="218.1"/>
      <line x1="0" y1="234.8" x2="132" y2="234.8"/><line x1="0" y1="251.5" x2="132" y2="251.5"/>
      <line x1="0" y1="268.2" x2="132" y2="268.2"/><line x1="0" y1="284.9" x2="132" y2="284.9"/>
      <line x1="0" y1="301.6" x2="132" y2="301.6"/><line x1="0" y1="317" x2="132" y2="317"/>
    </g>
  </svg>

  <svg class="plus-marks" viewBox="0 0 92 34" aria-hidden="true">
    <g stroke="var(--cream)" stroke-width="2">
      <line x1="0" y1="17" x2="34" y2="17"/><line x1="17" y1="0" x2="17" y2="34"/>
      <line x1="56" y1="17" x2="90" y2="17"/><line x1="73" y1="0" x2="73" y2="34"/>
    </g>
  </svg>

  <div class="hero-photo" role="img" aria-label="Top-down photo of a meal planning table: raw chicken breast, cherry tomatoes, spinach leaves, asparagus, walnuts and a notepad listing breakfast, lunch, dinner and snack"></div>

  <svg class="arc-text" viewBox="0 0 960 1200" aria-hidden="false">
    <defs>
      <path id="present-arc" d="M 502 458 A 418 418 0 0 1 1125 38"/>
    </defs>
    <text><textPath href="#present-arc">YOUR PRESENTS</textPath></text>
  </svg>

  <div class="tag-label">QUICK</div>
  <h1>
    <span class="title-top">GARDEN KITCHEN</span>
    <span class="title-main">MENU GUIDE</span>
  </h1>
  <p class="tagline">Your Belly Reset Starts Here</p>

  <div class="cta-band"></div>
  <p class="web-address">www.Loremipsum</p>
  <svg class="cta-arrow" viewBox="0 0 240 26" aria-hidden="true">
    <g stroke="var(--cream)" stroke-width="2" fill="none">
      <line x1="2" y1="13" x2="236" y2="13"/>
      <polyline points="223,1 236,13 223,25"/>
    </g>
  </svg>
</main>
</body>
</html>
```